Plakat für Hausverwaltung
Zielgruppe
Hausverwaltung
(Verwaltung von Wohn- und Gewerbeimmobilien)
Aufgabenstellung
Es soll ein Werbeplakat werden, Die Inhalte der Dienstleistung und die Firmenfarben kann der Webseite entnommen werden.
Ein guter Werbespruch und ansprechendes Desing ohne viel Schrift.

```html
<!DOCTYPE html>
<html lang="de">
<head>
<meta charset="utf-8">
<title>KWR Hausverwaltung – Plakat</title>
<link rel="stylesheet" href="https://fonts.googleapis.com/css2?family=Anton&family=Libre+Baskerville:wght@400;700&family=Poppins:wght@500;600;700&display=swap">
<style>
  :root {
    --stage: #9d9d9d;
    --paper: #f3f4f7;
    --paper-shade: #e4e6ea;
    --taupe: #857b70;
    --taupe-light: #cbc5bd;
    --taupe-band: #b7aea3;
    --ink: #38383a;
    --ink-soft: #4a4a4d;
    --charcoal: #444446;
    --white: #ffffff;
    --photo-a: #d9d2c6;
    --photo-b: #3b4352;
  }
  html, body {
    margin: 0;
    padding: 0;
    width: 923px;
    height: 1200px;
    overflow: hidden;
    background: var(--stage);
  }
  .poster {
    position: absolute;
    left: 30px;
    top: 300px;
    width: 863px;
    height: 601px;
    display: block;
  }
  .brand-name { font-family: "Poppins", sans-serif; font-weight: 600; font-size: 52px; fill: var(--ink); letter-spacing: 14px; }
  .brand-legal { font-family: "Libre Baskerville", serif; font-size: 22px; fill: var(--ink); }
  .offer-pill-label { font-family: "Libre Baskerville", serif; font-weight: 700; font-size: 35px; fill: var(--white); }
  .service { font-family: "Poppins", sans-serif; font-weight: 700; font-size: 26px; fill: var(--ink); }
  .headline { font-family: "Anton", sans-serif; font-size: 101px; }
  .headline-top { fill: var(--ink); }
  .headline-bottom { fill: var(--taupe); }
  .headline-sub { font-family: "Libre Baskerville", serif; font-weight: 700; font-size: 25px; fill: var(--ink-soft); }
  .contact { font-family: "Poppins", sans-serif; font-weight: 600; font-size: 30px; fill: var(--white); }
</style>
</head>
<body>
<svg class="poster" viewBox="0 0 1321 920" xmlns="http://www.w3.org/2000/svg">
  <defs>
    <linearGradient id="paperGrad" x1="0" y1="0" x2="1" y2="1">
      <stop offset="0" stop-color="#f7f8fa"/>
      <stop offset="1" stop-color="#e9ebef"/>
    </linearGradient>
    <linearGradient id="teamGrad" x1="0" y1="0" x2="1" y2="0">
      <stop offset="0" stop-color="var(--photo-a)"/>
      <stop offset="0.45" stop-color="#56607a"/>
      <stop offset="1" stop-color="var(--photo-b)"/>
    </linearGradient>
  </defs>

  <!-- background -->
  <rect class="paper" width="1321" height="920" fill="url(#paperGrad)"/>
  <polygon class="corner-band" points="0,0 620,0 0,105" fill="var(--taupe-light)"/>

  <!-- lower diagonal bands -->
  <polygon class="lower-field" points="0,680 1321,455 1321,920 0,920" fill="var(--paper-shade)"/>
  <polygon class="diagonal-band" points="0,640 1321,418 1321,452 0,676" fill="var(--taupe-band)"/>
  <polygon class="diagonal-line" points="0,684 1321,460 1321,466 0,690" fill="var(--white)"/>

  <!-- team photo area -->
  <polygon class="team-photo" role="img" aria-label="Teamfoto: drei Mitarbeitende der Hausverwaltung in Business-Kleidung"
           points="560,540 880,350 1321,380 1321,920 670,920" fill="url(#teamGrad)"/>

  <!-- contact panel -->
  <polygon class="contact-panel" points="0,700 395,637 670,920 0,920" fill="var(--charcoal)"/>

  <!-- brand -->
  <text class="brand-name" x="315" y="160" text-anchor="middle">KWR</text>
  <text class="brand-legal" x="315" y="198" text-anchor="middle">Haus- und Grundstücksverwaltungs GmbH</text>

  <!-- offers -->
  <rect class="offer-pill" x="85" y="252" width="416" height="60" rx="30" fill="var(--taupe)"/>
  <text class="offer-pill-label" x="293" y="295" text-anchor="middle">Unsere Angebote</text>

  <g class="tick" transform="translate(292,342)">
    <circle r="11" fill="var(--taupe)"/>
    <polyline points="-5,0 -1.5,4 5,-4" fill="none" stroke="#fff" stroke-width="2.5" stroke-linecap="round" stroke-linejoin="round"/>
  </g>
  <text class="service" x="292" y="390" text-anchor="middle">SONDEREIGENTUMVERWALTUNG</text>
  <g class="tick" transform="translate(292,420)">
    <circle r="11" fill="var(--taupe)"/>
    <polyline points="-5,0 -1.5,4 5,-4" fill="none" stroke="#fff" stroke-width="2.5" stroke-linecap="round" stroke-linejoin="round"/>
  </g>
  <text class="service" x="292" y="464" text-anchor="middle">WOHNEIGENTUMSVERWALTUNG</text>
  <g class="tick" transform="translate(292,490)">
    <circle r="11" fill="var(--taupe)"/>
    <polyline points="-5,0 -1.5,4 5,-4" fill="none" stroke="#fff" stroke-width="2.5" stroke-linecap="round" stroke-linejoin="round"/>
  </g>
  <text class="service" x="292" y="535" text-anchor="middle">MIETVERWALTUNG</text>

  <!-- headline -->
  <text class="headline headline-top" x="630" y="160" textLength="548" lengthAdjust="spacingAndGlyphs">IHRE IMMOBILIE</text>
  <text class="headline headline-bottom" x="628" y="274" textLength="607" lengthAdjust="spacingAndGlyphs">IN GUTEN HÄNDEN</text>
  <text class="headline-sub" x="631" y="318" textLength="609" lengthAdjust="spacingAndGlyphs">KWR Haus- und Immobilienverwaltungs GmbH</text>

  <!-- contacts -->
  <g class="contact-icon" transform="translate(102,750)">
    <circle r="17" fill="var(--taupe-light)"/>
    <path d="M-7,-8 l4,-1 3,5 -2.5,2 q2,4 5.5,5.5 l2,-2.5 5,3 -1,4 q-9,1 -16,-16z" fill="var(--charcoal)"/>
  </g>
  <text class="contact" x="135" y="761">06421 550290</text>
  <g class="contact-icon" transform="translate(102,802)">
    <circle r="17" fill="var(--taupe-light)"/>
    <rect x="-9" y="-6" width="18" height="12" fill="none" stroke="var(--charcoal)" stroke-width="1.6"/>
    <polyline points="-9,-6 0,1 9,-6" fill="none" stroke="var(--charcoal)" stroke-width="1.6"/>
  </g>
  <text class="contact" x="135" y="813">info@kwr-lahnstadt.de</text>
  <g class="contact-icon" transform="translate(102,851)">
    <circle r="17" fill="var(--taupe-light)"/>
    <circle r="9" fill="none" stroke="var(--charcoal)" stroke-width="1.6"/>
    <ellipse rx="4" ry="9" fill="none" stroke="var(--charcoal)" stroke-width="1.4"/>
    <line x1="-9" y1="0" x2="9" y2="0" stroke="var(--charcoal)" stroke-width="1.4"/>
  </g>
  <text class="contact" x="135" y="862">www.kwr-lahnstadt.de</text>
</svg>
</body>
</html>
```